Beauty Salon Treatment Menu & Pricing

We need a Treatment Pricelist/ Brochure made to hand out to potential & existing customers! Petalline Skin & Glow is a small friendly beauty salon focused on the beauty essentials such as waxing, spray tanning, facials & makeup. We have a webpage with our colour theme and style and we would like to brochure to tie in.
www.petallineskinandglow.com.au.
We like a brochure that is clean, simple and easy to read.

Industry/Entity Type

Beauty Salon

```html
<!DOCTYPE html>
<html lang="en">
<head>
<meta charset="utf-8">
<title>Petalline Skin &amp; Glow – Treatment Brochure</title>
<link rel="stylesheet" href="https://fonts.googleapis.com/css2?family=Poiret+One&family=Handlee&family=Roboto:wght@400;500&display=swap">
<style>
  :root{
    --red:#e0393f;
    --red-deep:#c42e34;
    --red-band:#d13138;
    --ink-light:#ffffff;
    --silver:#d8d8d8;
    --photo-light:#c9c9c9;
    --photo-dark:#5e5e5e;
    --page:#efeae4;
    --ornament-tone:#e8525f;
  }
  *{box-sizing:border-box;margin:0;padding:0}
  html,body{width:1200px;height:1024px;overflow:hidden}
  body{background:var(--page);position:relative;font-family:"Handlee",cursive;color:var(--ink-light)}

  .panel{
    position:absolute;top:52px;width:360px;height:920px;
    background:var(--red);
    box-shadow:0 6px 18px rgba(0,0,0,.18);
    display:flex;flex-direction:column;overflow:hidden;
  }
  .panel--cover{left:30px}
  .panel--intro{left:420px}
  .panel--services{left:810px}

  .brand{font-family:"Poiret One",sans-serif;font-weight:400;color:var(--ink-light);
    text-align:center;letter-spacing:1px;line-height:1.15;white-space:nowrap}
  .brand--large{font-size:31px}
  .brand--medium{font-size:28px}

  .photo-band{
    position:relative;height:230px;flex-shrink:0;
    background:linear-gradient(180deg,var(--silver) 0 8px,transparent 8px calc(100% - 8px),var(--silver) calc(100% - 8px));
    padding:8px 0;
  }
  .photo{
    width:100%;height:100%;
    background:linear-gradient(120deg,var(--photo-light),#9a9a9a 55%,var(--photo-dark));
  }

  /* Cover */
  .cover-top{position:relative;height:215px;flex-shrink:0;display:flex;align-items:flex-end;justify-content:center;padding-bottom:40px}
  .ornament-area{position:absolute;top:0;right:0;width:150px;height:120px;
    background:linear-gradient(200deg,var(--ornament-tone),var(--red) 85%)}
  .tagline{font-size:32px;line-height:1.3;text-align:center;padding:44px 26px 0}
  .phone{font-family:"Poiret One",sans-serif;font-size:38px;text-align:center;letter-spacing:2px;margin-top:auto;padding-bottom:22px}
  .cover-footer{background:var(--red-band);display:flex;font-family:"Roboto",sans-serif;font-size:11px;line-height:1.5;padding:12px 16px;gap:14px}
  .cover-footer h3{font-size:11px;font-weight:500;margin-bottom:3px}
  .contact{flex:1.1}
  .hours{flex:1}
  .web-strip{background:var(--silver);color:var(--red-deep);font-family:"Roboto",sans-serif;font-size:12px;text-align:center;padding:7px 0}

  /* Intro */
  .panel--intro .brand{padding-top:46px}
  .intro-text{font-size:19px;line-height:1.6;text-align:center;padding:30px 30px 0}
  .price-list{padding:0 34px;font-family:"Roboto",sans-serif;font-size:13px}
  .price-list--first{margin-top:48px}
  .price-list--last{margin-top:auto;padding-bottom:54px}
  .price-list h3{font-family:"Poiret One",sans-serif;font-size:24px;font-weight:400;letter-spacing:2px;margin-bottom:10px}
  .price-row{display:flex;justify-content:space-between;border-bottom:1px solid rgba(255,255,255,.3);padding:6px 0}

  /* Services */
  .services-title{font-family:"Poiret One",sans-serif;font-weight:400;font-size:27px;text-align:center;white-space:nowrap;padding:82px 0 62px}
  .services-text{font-size:19px;line-height:1.45;text-align:center;padding:36px 30px 0}
  .panel--services .brand{margin-top:auto;padding-bottom:40px}
</style>
</head>
<body>

<section class="panel panel--cover">
  <div class="cover-top">
    <div class="ornament-area" role="img" aria-label="Decorative floral vine with butterflies"></div>
    <div class="brand brand--large">Petalline Skin &amp; Glow</div>
  </div>
  <div class="photo-band">
    <div class="photo" role="img" aria-label="Black and white photo of a makeup artist applying eyeliner to a client"></div>
  </div>
  <p class="tagline">Everything you need at the one beauty appointment</p>
  <p class="phone">0400 555 218</p>
  <div class="cover-footer">
    <div class="contact">
      <h3>Contact Details</h3>
      <p>12 Lark Street, Bayview, WA, 6000 (Inside Willow Hair)</p>
    </div>
    <div class="hours">
      <h3>Opening Hours</h3>
      <p>Tue-Wed: 9:00 am - 5:00 pm</p>
      <p>Thu: 11:00 am - 8:00 pm</p>
      <p>Fri: 9:00 am - 5:00 pm</p>
      <p>Sat: 8:00 am - 2:00 pm</p>
    </div>
  </div>
  <div class="web-strip">www.petallineskinandglow.com.au</div>
</section>

<section class="panel panel--intro">
  <div class="brand brand--medium">Petalline Skin &amp; Glow</div>
  <p class="intro-text">Here at Petalline Skin &amp; Glow we strive to make sure you leave your appointment with expectations exceeded. We are a relaxed professional salon with a high percentage of returning clients. We tailor our services to you, ensuring our clients leave satisfied!</p>
  <div class="price-list price-list--first">
    <h3>Tanning</h3>
    <div class="price-row"><span>Full body tan</span><span>$35.00</span></div>
    <div class="price-row"><span>Half body tan</span><span>$25.00</span></div>
    <div class="price-row"><span>Express tan</span><span>$18.00</span></div>
  </div>
  <div class="price-list price-list--last">
    <h3>Waxing</h3>
    <div class="price-row"><span>Underarm</span><span>$15.00</span></div>
    <div class="price-row"><span>Stomach</span><span>$18.00</span></div>
    <div class="price-row"><span>Back</span><span>$30.00</span></div>
    <div class="price-row"><span>Patches, lip or chin</span><span>$10.00</span></div>
  </div>
</section>

<section class="panel panel--services">
  <h2 class="services-title">WAX TAN MAKEUP SKIN</h2>
  <div class="photo-band">
    <div class="photo" role="img" aria-label="Black and white photo of a makeup artist preparing a bride's makeup"></div>
  </div>
  <p class="services-text">Petalline Skin &amp; Glow offers everything you need at the one beauty appointment. Our staff are fully qualified professionals specialising is waxing, eyebrows, makeup, spray tanning and facial peel treatments. Only the highest quality products are used with the strictest level of health and hygiene maintained.</p>
  <div class="brand brand--medium">Petalline Skin &amp; Glow</div>
</section>

</body>
</html>
```